Research and Innovation programme/projects in WOOD based industries

1.Pramenova s.r.o. (offical registered brand name of our company)
-Managing technology development projects
-International cooperation and development European projects
Our company was founded in 2008 and started to work as a counsilary company operating in the section of european funds administrated by Czech republic. Nowadays we are specializing on projects in the sphere of science and research co-financed by EU.Since 6.6.2013 we are registered under European comission for a purpose of broad support of transnational projects.

Target Market(s)

We are primarily focused on european companies, which stand behind the latest research and innovation of sawing, planing, glulam and logging technologies based on wooden materials.

Coding

Coded - Design and coding required

Number of Pages Required

5+ page

Font styles to use
Serif

Colors
cadf82
abd037
9bcb3c
fee18a
ffcf3e
ffc214

Requirements
Must have
• The web will exist in three possible languages in czech, english and deutsch.
• First page : introduction of a company
• Second page : Area of expertise
• Third page: servicies our company provides
• Fourth page: Our partners
• Fifth page: Conditions of our servicies
• Sixth page: Succesful projects
• - we would also love if we had possibility to add videos about our successful projects
• Seventh: Our team
• We are serious company in the sphere of funds and counsilary servicies, that is why we would love to have web design as representative as possible
• Take on mind that that we are specializing on development management, try to apply that on your design
• In the section of contacts, we would love to have photos of our team,
• This is our current site: http://www.pramenova-example.eu/cz/partneri.html
• This is how our concurency sites are lookin. Take these designs as an slight inspiration.
• http://www.lumatrava-example.sk/en/
• https://www2.brenvick-example.com/global/en.html
Nice to have
• Visible logo on the front page for the visitor.
• As a inspiration we provided link for our current web design, but we dont want to copy the current style, just look at the logo and the pages that exists on current web.
• !!!!!!We also uploaded file, where we explain how our cooperation with partner works. Especially in the part 2. section of service. Take that as an ispiration too, or use that to understand, what our company do.
Should not have
• We are serious company in the sphere of funds and counsilary servicies, that is why we would love to have web design representative as possible

```html
<!DOCTYPE html>
<html lang="en">
<head>
<meta charset="utf-8">
<title>Pramenova s.r.o. – Beratungsfirma</title>
<link href="https://fonts.googleapis.com/css2?family=Montserrat:wght@500;600;700&family=Open+Sans:wght@400;600;700&display=swap" rel="stylesheet">
<style>
:root{
  --green:#7dc243;
  --green-dark:#5fa52d;
  --orange:#f7941d;
  --orange-bright:#ff9b1a;
  --ink:#1f1f1f;
  --text:#555;
  --muted:#8a8a8a;
  --line:#d9d9d9;
  --wood-dark:#4a2616;
  --wood:#6e3a22;
  --wood-light:#b8652a;
  --wood-light-dark:#9a5322;
  --footer:#1d1d1f;
  --white:#fff;
}
*{box-sizing:border-box;margin:0;padding:0}
html,body{width:1200px;height:4435px;overflow:hidden}
body{font-family:"Open Sans",Arial,sans-serif;color:var(--text);background:var(--white);position:relative}
.section{position:absolute;left:0;width:1200px}
.section-bg{position:absolute;inset:0}
.bg-wood{background:linear-gradient(180deg,var(--wood) 0%,#74402a 50%,var(--wood-dark) 100%)}
.bg-wood-light{background:linear-gradient(180deg,#c0702f,var(--wood-light) 50%,var(--wood-light-dark))}
.h-title{font-family:"Montserrat",Arial,sans-serif;font-weight:700;text-transform:uppercase;text-align:center;font-size:38px;letter-spacing:.5px}
.btn{display:inline-flex;align-items:center;justify-content:center;gap:8px;background:var(--orange);color:var(--white);font-family:"Montserrat",sans-serif;font-weight:700;text-transform:uppercase;font-size:14px;border-radius:2px;text-decoration:none}
.arrow{position:absolute;width:44px;height:44px;border-radius:50%;border:2px solid rgba(255,255,255,.85);display:flex;align-items:center;justify-content:center;color:var(--white)}
.arrow.dark{border-color:#555;color:#333}
.arrow svg{width:16px;height:10px}

/* header */
.header{top:0;height:100px}
.logo{position:absolute;left:110px;top:30px;display:flex;gap:10px;align-items:center}
.logo-mark{width:50px;height:34px;background:var(--green)}
.logo-name{font-family:"Montserrat",sans-serif;font-weight:700;font-size:17px;color:var(--green-dark);line-height:1}
.logo-sub{font-family:"Montserrat",sans-serif;font-weight:600;font-size:13px;color:var(--orange);margin-top:4px}
.lang{position:absolute;left:713px;top:12px;width:87px;height:34px;border:1px solid #bbb;font-size:14px;display:flex;align-items:center;padding-left:10px;gap:6px;color:#333}
.lang .flag{width:14px;height:10px;background:#c33}
.search{position:absolute;left:830px;top:12px;width:258px;height:34px;border:1px solid #bbb;display:flex}
.search span{flex:1;padding:7px 12px;font-size:13px;color:#999}
.search i{width:38px;background:#777;display:flex;align-items:center;justify-content:center}
.nav{position:absolute;left:375px;top:64px;display:flex;gap:19px;font-family:"Montserrat",sans-serif;font-weight:600;font-size:15px;color:var(--ink)}
.nav .active{background:var(--green);padding:0 2px}
.signup{position:absolute;left:992px;top:58px;width:96px;height:36px}

/* hero */
.hero{top:100px;height:506px}
.hero-bg{background:linear-gradient(135deg,#6e6a64,#a59c8e 40%,#6f5a3e 70%,#4d4a47)}
.hero-shade{position:absolute;left:310px;top:112px;width:580px;height:200px;background:rgba(0,0,0,.3)}
.hero h1{position:absolute;top:135px;width:100%;text-align:center;font-family:"Montserrat",sans-serif;font-weight:700;font-size:50px;color:var(--white);letter-spacing:1px}
.hero p{position:absolute;top:214px;width:100%;text-align:center;color:var(--white);font-size:19px;line-height:34px}
.hero .btn{position:absolute;left:520px;top:310px;width:160px;height:48px;font-size:16px;background:var(--orange-bright)}
.dots{position:absolute;top:472px;left:566px;display:flex;gap:4px}
.dots b{width:10px;height:10px;border-radius:50%;border:1.5px solid var(--white)}
.dots b.on{background:var(--white)}

/* welcome */
.welcome{top:606px;height:527px}
.welcome .frame{position:absolute;left:116px;top:118px;width:390px;height:268px;border:3px solid var(--green)}
.welcome .photo{position:absolute;left:110px;top:130px;width:385px;height:262px;background:linear-gradient(160deg,#3a3a3a,#8c8a84 45%,#5a4a38)}
.welcome .kicker{position:absolute;left:590px;top:95px;font-size:22px;color:var(--ink)}
.welcome h2{position:absolute;left:590px;top:124px;font-family:"Montserrat",sans-serif;font-weight:700;font-size:38px;color:var(--ink)}
.welcome p{position:absolute;left:590px;top:188px;width:500px;font-size:14px;line-height:29px;color:var(--muted)}
.welcome .btn{position:absolute;left:590px;top:392px;width:142px;height:42px}

.expertise{top:1133px;height:525px}
.expertise h2{position:absolute;top:82px;width:100%;color:var(--white)}
.expertise .lead{position:absolute;top:138px;width:100%;text-align:center;color:var(--white);font-size:14px;line-height:28px}
.cards3{position:absolute;left:110px;top:222px;display:flex;gap:21px}
.photo-card{width:312px;height:212px;border:3px solid #eee;position:relative}
.photo-card .overlay{position:absolute;inset:0;background:rgba(40,40,40,.55);color:var(--white);text-align:center;padding-top:28px}
.photo-card .overlay h3{font-family:"Montserrat",sans-serif;font-weight:600;font-size:16px;margin-bottom:10px}
.photo-card .overlay p{font-size:14px;line-height:26px;padding:0 12px}
.photo-card .overlay a{display:block;margin-top:12px;color:var(--orange);font-family:"Montserrat",sans-serif;font-weight:700;font-size:13px}

/* services */
.services{top:1658px;height:560px}
.services h2{position:absolute;top:82px;width:100%;color:var(--ink)}
.services .lead{position:absolute;top:143px;width:100%;text-align:center;font-size:14px;line-height:28px;color:var(--muted)}
.svc-list{position:absolute;left:110px;top:217px;display:flex;gap:14px}
.svc{width:234px;height:251px;border:2px solid var(--line);text-align:center;padding-top:16px}
.svc svg{width:56px;height:56px}
.svc h3{font-family:"Montserrat",sans-serif;font-weight:600;font-size:15px;color:var(--ink);margin:12px 0 10px}
.svc p{font-size:14px;line-height:26px;color:var(--text);padding:0 10px}
.svc a{display:block;margin-top:18px;color:var(--orange);font-family:"Montserrat",sans-serif;font-weight:700;font-size:13px}

/* partners */
.partners{top:2218px;height:258px}
.partners h2{position:absolute;top:46px;width:100%;color:var(--white)}
.partner-row{position:absolute;top:138px;left:180px;width:840px;display:flex;justify-content:space-around;align-items:center}
.partner{display:flex;align-items:center;gap:10px;font-family:"Montserrat",sans-serif;font-weight:600;font-size:22px;color:var(--white)}
.partner i{width:22px;height:22px;background:var(--white)}

/* conditions */
.conditions{top:2476px;height:506px}
.conditions .kicker{position:absolute;left:110px;top:88px;font-family:"Montserrat",sans-serif;font-size:24px;color:var(--ink)}
.conditions h2{position:absolute;left:110px;top:118px;font-family:"Montserrat",sans-serif;font-weight:700;font-size:40px;color:var(--ink)}
.conditions ul{position:absolute;left:110px;top:182px;list-style:none}
.conditions li{display:flex;align-items:center;gap:8px;font-size:14px;line-height:30px;color:var(--text)}
.conditions li svg{width:16px;height:14px}
.conditions .frame{position:absolute;left:692px;top:124px;width:390px;height:258px;border:5px solid var(--green);border-right:0;border-bottom:0}
.conditions .photo{position:absolute;left:702px;top:134px;width:386px;height:256px;background:linear-gradient(170deg,#9aa3a8,#d8d4cc 45%,#7a7672)}

/* projects */
.projects{top:2982px;height:465px}
.projects h2{position:absolute;top:68px;width:100%;color:var(--white);line-height:48px}
.projects .cards3{top:189px}
.play{position:absolute;left:50%;top:50%;width:36px;height:36px;margin:-18px 0 0 -18px;border-radius:50%;background:var(--green);display:flex;align-items:center;justify-content:center}

/* team */
.team{top:3447px;height:619px}
.team h2{position:absolute;top:84px;width:100%;color:var(--ink)}
.member{position:absolute;top:183px;width:300px;text-align:center}
.avatar{position:relative;width:196px;height:196px;margin:0 auto;border-radius:50%;border:2px solid var(--green);padding:8px}
.avatar .ph{width:100%;height:100%;border-radius:50%}
.soc{position:absolute;width:30px;height:30px;border-radius:50%;border:2px solid var(--green);background:var(--white);display:flex;align-items:center;justify-content:center;font-size:12px;font-weight:700;color:#333}
.member h3{margin-top:34px;font-family:"Montserrat",sans-serif;font-weight:600;font-size:16px;color:var(--ink)}
.member .role{font-size:14px;color:var(--muted);margin-top:4px}
.member .btn{margin-top:22px;width:137px;height:42px}

/* footer */
.footer{top:4066px;height:369px;background:linear-gradient(180deg,#222226,var(--footer))}
.fcol{position:absolute;top:56px;color:var(--white)}
.fcol h4{font-family:"Montserrat",sans-serif;font-weight:600;font-size:14px;margin-bottom:18px}
.fcol a{display:block;font-size:13px;line-height:27px;color:#ddd;text-decoration:none}
.contact{display:flex;gap:14px;font-size:13px;line-height:23px;color:#ddd;margin-bottom:8px}
.contact svg{width:12px;height:14px;margin-top:5px;flex:none}
.social{display:flex;gap:14px}
.social span{width:36px;height:36px;border-radius:50%;border:1.5px solid #bbb;display:flex;align-items:center;justify-content:center;font-size:12px;font-weight:700;color:var(--white)}
.fline{position:absolute;left:110px;top:290px;width:978px;height:1px;background:#444}
.fmark{position:absolute;left:574px;top:276px;width:52px;height:32px;background:var(--green)}
.copy{position:absolute;top:326px;width:100%;text-align:center;font-size:13px;color:#ddd}
</style>
</head>
<body>

<header class="section header">
  <div class="logo">
    <span class="logo-mark"></span>
    <div><div class="logo-name">Pramenova s.r.o.</div><div class="logo-sub">Beratungsfirma</div></div>
  </div>
  <div class="lang"><span class="flag"></span>Eng ▾</div>
  <div class="search"><span>Search</span><i><svg width="14" height="14" viewBox="0 0 14 14"><circle cx="6" cy="6" r="4.5" fill="none" stroke="#fff" stroke-width="2"/><path d="M9.5 9.5L13 13" stroke="#fff" stroke-width="2"/></svg></i></div>
  <nav class="nav">
    <span class="active">Home</span><span>Services</span><span>Our Projects</span><span>Partners</span><span>Business Conditions</span><span>Contacts</span>
  </nav>
  <a class="btn signup">Sign Up</a>
</header>

<section class="section hero">
  <div class="section-bg hero-bg" role="img" aria-label="Wood processing workshop with stacked boards and machinery"></div>
  <div class="hero-shade"></div>
  <h1>PRAMENOVA</h1>
  <p>Sed ut perspiciatis unde omnis iste natus error sit voluptatem<br>accusantium doloremque laudantium, totam rem aperiam,</p>
  <a class="btn">Get Started</a>
  <div class="dots"><b></b><b></b><b class="on"></b><b></b><b></b></div>
</section>

<section class="section welcome">
  <div class="frame"></div>
  <div class="photo" role="img" aria-label="Factory hall with timber production line"></div>
  <div class="kicker">Welcome To</div>
  <h2>PRAMENOVA</h2>
  <p>Sed ut perspiciatis unde omnis iste natus error voluptatem accusantium doloremque laudantium, totam rem aperiam, eaque ipsa quae inventore veritatis et quasi architecto beatae vitae dicta sunt explicabo. Nemo enim ipsam voluptatem quia voluptas sit aspernatur aut odit aut fugit sed quia consequuntur magni dolores eos qui ratione voluptatem sequi nesciunt. Neque porro quisquam est, qui dolorem</p>
  <a class="btn">Learn More ⊕</a>
</section>

<section class="section expertise">
  <div class="section-bg bg-wood" role="img" aria-label="Dark wooden plank background"></div>
  <h2 class="h-title">Area of Expertise</h2>
  <p class="lead">Nemo enim ipsam voluptatem quia voluptas sit aspernatur aut odit aut fugit, consequuntur<br>magni dolores eos qui ratione voluptatem sequi nesciunt. Neque porro quisquam</p>
  <div class="arrow" style="left:33px;top:305px"><svg viewBox="0 0 16 10"><path d="M15 5H2M5 1L1 5l4 4" stroke="#fff" stroke-width="2" fill="none"/></svg></div>
  <div class="cards3">
    <div class="photo-card" role="img" aria-label="Timber frame building under construction" style="background:linear-gradient(180deg,#6fa3d6 0 35%,#b07a4a 35%,#8a5a35)"></div>
    <div class="photo-card" role="img" aria-label="Industrial wood warehouse interior" style="background:linear-gradient(180deg,#7a7a7a,#4a4038)">
      <div class="overlay"><h3>INDUSTRIAL</h3><p>Nor again is there anyone who loves or pursues or desires to obtain pain of itself,</p><a>LEARN MORE ⊕</a></div>
    </div>
    <div class="photo-card" role="img" aria-label="Wooden school desks in a classroom" style="background:linear-gradient(160deg,#d8cfc2,#a7794c 60%,#6b4a2e)"></div>
  </div>
  <div class="arrow" style="left:1121px;top:305px"><svg viewBox="0 0 16 10"><path d="M1 5h13M11 1l4 4-4 4" stroke="#fff" stroke-width="2" fill="none"/></svg></div>
</section>

<section class="section services">
  <h2 class="h-title">Our Services</h2>
  <p class="lead">Sed ut perspiciatis unde omnis iste natus error sit voluptatem accusantium doloremque<br>laudantium, totam rem aperiam, eaque ipsa quae ab illo inventore veritatis</p>
  <div class="arrow dark" style="left:33px;top:320px"><svg viewBox="0 0 16 10"><path d="M15 5H2M5 1L1 5l4 4" stroke="#333" stroke-width="2" fill="none"/></svg></div>
  <div class="svc-list">
    <div class="svc">
      <svg viewBox="0 0 56 56" fill="none" stroke="#444" stroke-width="1.6"><circle cx="14" cy="14" r="8"/><circle cx="42" cy="14" r="8"/><circle cx="14" cy="42" r="8"/><circle cx="42" cy="42" r="8"/><rect x="22" y="22" width="12" height="12"/><path d="M20 20l3 3M36 20l-3 3M20 36l3-3M36 36l-3-3"/></svg>
      <h3>Project coordination</h3><p>Nor again is there anyone who loves or pursues or desires to obtain pain of itself</p><a>READ MORE ⟶</a>
    </div>
    <div class="svc">
      <svg viewBox="0 0 56 56" fill="none" stroke="#444" stroke-width="1.6"><path d="M14 10h20l8 8v30H14z"/><path d="M20 24h16M20 30h16M20 36h10M22 44l4-4 4 3 6-6"/><circle cx="40" cy="12" r="5"/></svg>
      <h3>Project financing</h3><p>Nor again is there anyone who loves or pursues or desires to obtain pain of itself</p><a>READ MORE ⟶</a>
    </div>
    <div class="svc">
      <svg viewBox="0 0 56 56" fill="none" stroke="#444" stroke-width="1.6"><circle cx="24" cy="28" r="16"/><path d="M8 28h32M24 12c-7 8-7 24 0 32M24 12c7 8 7 24 0 32"/><circle cx="42" cy="34" r="6"/><path d="M42 40v6"/></svg>
      <h3>Technology and foreign trade</h3><p>Nor again is there anyone who loves or pursues or desires to obtain pain of itself</p><a>READ MORE ⟶</a>
    </div>
    <div class="svc">
      <svg viewBox="0 0 56 56" fill="none" stroke="#444" stroke-width="1.6"><path d="M28 38V12M20 20l8-8 8 8M14 34v10h28V34"/></svg>
      <h3>Export promotion</h3><p>Nor again is there anyone who loves or pursues or desires to obtain pain of itself</p><a>READ MORE ⟶</a>
    </div>
  </div>
  <div class="arrow dark" style="left:1121px;top:320px"><svg viewBox="0 0 16 10"><path d="M1 5h13M11 1l4 4-4 4" stroke="#333" stroke-width="2" fill="none"/></svg></div>
</section>

<section class="section partners">
  <div class="section-bg bg-wood-light" role="img" aria-label="Light wooden plank background"></div>
  <h2 class="h-title">Our Partners</h2>
  <div class="arrow" style="left:33px;top:107px"><svg viewBox="0 0 16 10"><path d="M15 5H2M5 1L1 5l4 4" stroke="#fff" stroke-width="2" fill="none"/></svg></div>
  <div class="partner-row">
    <div class="partner"><i></i>Norvale Invest</div>
    <div class="partner"><i></i>Tradeline</div>
    <div class="partner"><i></i>Chamber Union</div>
  </div>
  <div class="arrow" style="left:1121px;top:107px"><svg viewBox="0 0 16 10"><path d="M1 5h13M11 1l4 4-4 4" stroke="#fff" stroke-width="2" fill="none"/></svg></div>
</section>

<section class="section conditions">
  <div class="kicker">CONDITIONS OF</div>
  <h2>OUR SERVICES</h2>
  <ul>
    <li><svg viewBox="0 0 16 14"><path d="M1 7l5 5L15 1" stroke="#7dc243" stroke-width="2.4" fill="none"/></svg>Sed ut perspiciatis unde omnis iste natus error sit voluptatem</li>
    <li><svg viewBox="0 0 16 14"><path d="M1 7l5 5L15 1" stroke="#7dc243" stroke-width="2.4" fill="none"/></svg>Accusantium doloremque laudantium, totam rem aperiam, eaque</li>
    <li><svg viewBox="0 0 16 14"><path d="M1 7l5 5L15 1" stroke="#7dc243" stroke-width="2.4" fill="none"/></svg>Quae ab illo inventore veritatis et quasi architecto beatae vitae dicta.</li>
    <li><svg viewBox="0 0 16 14"><path d="M1 7l5 5L15 1" stroke="#7dc243" stroke-width="2.4" fill="none"/></svg>Nemo enim ipsam voluptatem quia voluptas sit aspernatur</li>
    <li><svg viewBox="0 0 16 14"><path d="M1 7l5 5L15 1" stroke="#7dc243" stroke-width="2.4" fill="none"/></svg>Fugit, sed quia consequuntur magni dolores eos qui ratione</li>
    <li><svg viewBox="0 0 16 14"><path d="M1 7l5 5L15 1" stroke="#7dc243" stroke-width="2.4" fill="none"/></svg>Voluptatem &nbsp;Neque porro quisquam est, qui dolorem ipsum quia</li>
    <li><svg viewBox="0 0 16 14"><path d="M1 7l5 5L15 1" stroke="#7dc243" stroke-width="2.4" fill="none"/></svg>Consectetur, adipisci velit, sed quia non numquam eius modi</li>
    <li><svg viewBox="0 0 16 14"><path d="M1 7l5 5L15 1" stroke="#7dc243" stroke-width="2.4" fill="none"/></svg>Ncidunt ut labore et dolore magnam aliquam quaerat voluptatem.</li>
  </ul>
  <div class="frame"></div>
  <div class="photo" role="img" aria-label="Modern multi-storey office building"></div>
</section>

<section class="section projects">
  <div class="section-bg bg-wood" role="img" aria-label="Dark wooden plank background"></div>
  <h2 class="h-title">Our Successful<br>Projects</h2>
  <div class="arrow" style="left:33px;top:267px"><svg viewBox="0 0 16 10"><path d="M15 5H2M5 1L1 5l4 4" stroke="#fff" stroke-width="2" fill="none"/></svg></div>
  <div class="cards3">
    <div class="photo-card" role="img" aria-label="Video: timber storage warehouse" style="background:linear-gradient(180deg,#cfd6dc,#c9a46a 55%,#8a8e92)"><span class="play"><svg width="14" height="14" viewBox="0 0 14 14"><path d="M3 1l10 6-10 6z" fill="#fff"/></svg></span></div>
    <div class="photo-card" role="img" aria-label="Video: wooden clad modern house" style="background:linear-gradient(180deg,#d9dde2,#8a4d2a 45%,#4a2c1c)"><span class="play"><svg width="14" height="14" viewBox="0 0 14 14"><path d="M3 1l10 6-10 6z" fill="#fff"/></svg></span></div>
    <div class="photo-card" role="img" aria-label="Video: completed office building" style="background:linear-gradient(180deg,#b9b6ae,#8d8a84 60%,#6a6660)"><span class="play"><svg width="14" height="14" viewBox="0 0 14 14"><path d="M3 1l10 6-10 6z" fill="#fff"/></svg></span></div>
  </div>
  <div class="arrow" style="left:1121px;top:267px"><svg viewBox="0 0 16 10"><path d="M1 5h13M11 1l4 4-4 4" stroke="#fff" stroke-width="2" fill="none"/></svg></div>
</section>

<section class="section team">
  <h2 class="h-title">Our Team</h2>
  <div class="member" style="left:108px">
    <div class="avatar"><div class="ph" role="img" aria-label="Portrait of Marek Holan" style="background:linear-gradient(160deg,#6c5a4a,#3e3a38)"></div>
      <span class="soc" style="right:-14px;top:30px">f</span><span class="soc" style="right:-28px;top:84px">◎</span><span class="soc" style="right:-14px;top:138px">t</span></div>
    <h3>MAREK HOLAN</h3><div class="role">Executive Director</div><a class="btn">More Info ⊕</a>
  </div>
  <div class="member" style="left:425px">
    <div class="avatar"><div class="ph" role="img" aria-label="Portrait of Jana Sedlova" style="background:linear-gradient(160deg,#c9dbe8,#6a5446)"></div>
      <span class="soc" style="right:-14px;top:30px">f</span><span class="soc" style="right:-28px;top:84px">◎</span><span class="soc" style="right:-14px;top:138px">t</span></div>
    <h3>JANA SEDLOVA</h3><div class="role">Project manager</div><a class="btn">More Info ⊕</a>
  </div>
  <div class="member" style="left:742px">
    <div class="avatar"><div class="ph" role="img" aria-label="Portrait of Pavel Kroupa" style="background:linear-gradient(160deg,#9aa6b0,#4a5460)"></div>
      <span class="soc" style="right:-14px;top:30px">f</span><span class="soc" style="right:-28px;top:84px">◎</span><span class="soc" style="right:-14px;top:138px">t</span></div>
    <h3>PAVEL KROUPA</h3><div class="role">project consultant</div><a class="btn">More Info ⊕</a>
  </div>
</section>

<footer class="section footer">
  <div class="fcol" style="left:110px"><h4>QUICK LINKS</h4><a>Home</a><a>Services</a><a>Our Projects</a><a>Partners</a><a>Conditions</a><a>Contacts</a></div>
  <div class="fcol" style="left:318px"><h4>SERVICES</h4><a>project coordination</a><a>project financing</a><a>Technology and foreign trade</a><a>Projects in the framework of</a><a>international cooperation</a><a>EU projects</a></div>
  <div class="fcol" style="left:630px"><h4>COME FIND US</h4>
    <div class="contact"><svg viewBox="0 0 12 14"><path d="M6 13S1 8 1 5a5 5 0 0110 0c0 3-5 8-5 8z" fill="#ddd"/><circle cx="6" cy="5" r="1.8" fill="#222"/></svg><span>At vero eos et accusamus<br>et iusto odio</span></div>
    <div class="contact"><svg viewBox="0 0 12 14"><rect x="1" y="3" width="10" height="8" fill="none" stroke="#ddd" stroke-width="1.3"/><path d="M1 3l5 4 5-4" stroke="#ddd" stroke-width="1.3" fill="none"/></svg><span>holan@pramenova-example.eu</span></div>
    <div class="contact"><svg viewBox="0 0 12 14"><path d="M2 2l3 0 1 3-2 1c1 2 2 3 4 4l1-2 3 1v3c-6 0-10-4-10-10z" fill="#ddd"/></svg><span>420 555 010 200</span></div>
  </div>
  <div class="fcol" style="left:955px"><h4>STAY CONNECTED</h4><div class="social"><span>f</span><span>t</span><span>in</span></div></div>
  <div class="fline"></div>
  <div class="fmark"></div>
  <div class="copy">Copyright © 2019 pramenova. All Rights Reserved</div>
</footer>

</body>
</html>
```